Velvet Riot Rising Line of Sparkling Wine & Spirits

Back info: Nora Beth Quill Owner 555-318-4402 1480 E. Harlow Ave, Bldg. 2, & 3, Lodi Ca. 95871
Sparkling Wines & Memorabilia www.velvetriotrising.com
Ok I have uploaded the winning design. The color that I am after is the Fushia, Raspberry, Red, Matte Satin Matalic Finish. With a 24 Karet Gold color Foil. The Bottle is on the top row and it's the 2nd Bottle in. That is the Color that I want. This is the style of font. Make sure that you put what we're advertising. Good Luck to you all. Warmest regards, Nora
21 & up UniSex
Sparkling Wine and Memorabilia
there listed up above.....

```html
<!DOCTYPE html>
<html lang="en">
<head>
<meta charset="utf-8">
<title>Velvet Riot Rising — Business Card</title>
<link rel="stylesheet" href="https://fonts.googleapis.com/css2?family=Arimo:wght@400;700&display=swap">
<style>
  :root {
    --page: #e9e9e9;
    --card-white: #ffffff;
    --raspberry-deep: #8e1450;
    --raspberry-mid: #b81c72;
    --fuchsia-glow: #e31f96;
    --gold-foil: #f2c84e;
    --ink-white: #ffffff;
    --ink-charcoal: #3a3a3a;
    --ink-grey: #2f2f2f;
    --rule-grey: #bdbdbd;
  }
  * { margin: 0; padding: 0; box-sizing: border-box; }
  html, body {
    width: 1200px; height: 1200px; overflow: hidden;
    background: var(--page);
    font-family: "Arimo", Arial, sans-serif;
  }
  .canvas { position: relative; width: 1200px; height: 1200px; }

  .card {
    position: absolute;
    width: 688px; height: 393px;
    background: var(--card-white);
    overflow: hidden;
  }
  .card--front { left: 267px; top: 159px; }
  .card--back { left: 262px; top: 653px; }

  .front-panel {
    position: absolute; left: 0; top: 0;
    width: 432px; height: 100%;
    background: radial-gradient(ellipse 300px 260px at 160px 200px,
      var(--fuchsia-glow) 0%, var(--raspberry-mid) 55%, var(--raspberry-deep) 100%);
  }
  .bottle-art {
    position: absolute;
    border-radius: 14px 14px 10px 10px;
    background: linear-gradient(90deg, #a8105f 0%, var(--fuchsia-glow) 45%, #c2147a 100%);
  }
  .card--front .bottle-art { left: 392px; top: 0; width: 123px; height: 393px; border: 2px solid #fff; }
  .card--back .bottle-art { left: 91px; top: 69px; width: 81px; height: 262px; }

  .contact { position: absolute; left: 52px; top: 100px; color: var(--ink-white); }
  .contact__name {
    font-weight: 700; font-size: 26px; color: var(--gold-foil);
    letter-spacing: 0.2px; line-height: 1;
  }
  .contact__role { font-size: 17px; margin-top: 2px; }
  .contact__address { font-size: 16px; line-height: 21px; margin-top: 28px; }
  .contact__lines { margin-top: 29px; font-size: 16px; line-height: 21px; }
  .contact__line { display: flex; align-items: center; gap: 10px; }
  .contact__line svg { width: 14px; height: 14px; flex: none; }

  .brand-name {
    position: absolute; left: 192px; top: 165px;
    font-weight: 700; font-size: 42px; color: var(--ink-charcoal);
    line-height: 1; white-space: nowrap;
  }
  .brand-rule {
    position: absolute; left: 183px; top: 228px; width: 438px; height: 1px;
    background: linear-gradient(90deg, transparent 0%, var(--rule-grey) 10%, var(--rule-grey) 80%, transparent 100%);
  }
  .tagline {
    position: absolute; left: 192px; top: 239px;
    font-size: 17px; letter-spacing: 2px; color: var(--ink-grey); white-space: nowrap;
  }
  .tagline__accent { color: var(--fuchsia-glow); font-weight: 700; }
  .card--back .edge-band {
    position: absolute; left: 0; bottom: 0; width: 100%; height: 2px; background: var(--raspberry-mid);
  }
</style>
</head>
<body>
<main class="canvas">
  <section class="card card--front">
    <div class="front-panel"></div>
    <div class="bottle-art" role="img" aria-label="Satin fuchsia sparkling wine bottle with black and gold crest label"></div>
    <div class="contact">
      <p class="contact__name">NORA BETH QUILL</p>
      <p class="contact__role">Owner</p>
      <p class="contact__address">E. Harlow Ave<br>Bldg. 2, &amp; 3, Lodi Ca. 95871</p>
      <div class="contact__lines">
        <p class="contact__line">
          <svg viewBox="0 0 16 16" aria-hidden="true"><path fill="var(--gold-foil)" d="M3.2 1.2l2.3-.4 1.4 3.3-1.6 1.3c.8 1.8 2.2 3.3 4.1 4.2l1.3-1.6 3.3 1.4-.4 2.3c-.2.9-1 1.5-1.9 1.4C6.3 12.7 2.5 8.6 1.9 3.1c-.1-.9.4-1.7 1.3-1.9z"/></svg>
          <span>555-318-4402 1480</span>
        </p>
        <p class="contact__line">
          <svg viewBox="0 0 16 16" aria-hidden="true"><circle cx="8" cy="8" r="7" fill="var(--gold-foil)"/><path d="M4 5c2 0 2 2 3.5 2S8 9.5 6.5 10 5 13 5 13M10 3c-.5 1.5 1 2 2 2.5s1 2 0 3" fill="none" stroke="var(--raspberry-mid)" stroke-width="1.3"/></svg>
          <span>www.velvetriotrising.com</span>
        </p>
      </div>
    </div>
  </section>

  <section class="card card--back">
    <div class="bottle-art" role="img" aria-label="Satin fuchsia sparkling wine bottle with black and gold crest label"></div>
    <p class="brand-name">Velvet Riot Rising</p>
    <div class="brand-rule"></div>
    <p class="tagline">SPARKLING <span class="tagline__accent">WINES &amp; MEMORABILIA</span></p>
    <div class="edge-band"></div>
  </section>
</main>
</body>
</html>
```